Business cards for 3 Realtors at one brokerage

We will need a business card template that can be projected on 3 business cards. Harborline Realty & Investment Corp. has 3 realtors on staff Dane, Owen, and Miles. We all want a business card that shows our new logo and information. I will attach many versions of our Logo as well as head shots for each realtor (Owen- Long hair, youngest. Miles- Suit jacket, parted hair cut. Dane- Angled Pose, Shirt and Tie.) I have attached our information below.

Dane Foskett
801-555-0147
dane@harborlinehomesite.com
Principal Broker

Miles Tandrow
801-555-0162
miles@harborlinehomesite.com
Real Estate Agent

Owen Tandrow
801-555-0138
owen@harborlinehomesite.com
Real Estate Agent

Harborline Realty & Investment Corp.
HarborlineHomesite.com
5286 N 7200 Suite 208-617, South Jordan, UT 84009

Please feel free to reach out with any questions, comments, or concerns.

```html
<!DOCTYPE html>
<html lang="en">
<head>
<meta charset="utf-8">
<title>Harborline Realty – Business Card</title>
<link rel="stylesheet" href="https://fonts.googleapis.com/css2?family=Montserrat:wght@400;500;600;700&display=swap">
<style>
  :root {
    --backdrop: #bdbdbd;
    --card: #1c1d1f;
    --edge: #2f86cf;
    --accent: #3aa4ec;
    --brand-grey: #9a9c9f;
    --text: #e6e7e8;
    --muted: #8c8e91;
    --photo-top: #3a3b3e;
    --photo-mid: #8a8d93;
    --pattern-a: #26272a;
    --pattern-b: #121314;
  }
  * { box-sizing: border-box; margin: 0; padding: 0; }
  html, body { width: 1200px; height: 800px; overflow: hidden; }
  body {
    background: var(--backdrop);
    font-family: "Montserrat", sans-serif;
    position: relative;
  }
  .card {
    position: absolute;
    width: 540px;
    height: 308px;
    border-radius: 18px;
    background: var(--card);
    border-bottom: 3px solid var(--edge);
    border-left: 2px solid var(--edge);
    overflow: hidden;
    top: 246px;
  }
  .card--front { left: 40px; }
  .card--back { left: 620px; }

  .brand {
    position: absolute;
    left: 30px;
    top: 34px;
    display: flex;
    align-items: center;
    gap: 12px;
  }
  .brand__dot {
    width: 46px; height: 46px;
    border: 4px solid var(--accent);
    border-radius: 50%;
    flex-shrink: 0;
  }
  .brand__name {
    color: var(--brand-grey);
    font-weight: 600;
    font-size: 14px;
    letter-spacing: 1.5px;
    line-height: 1.3;
    text-transform: uppercase;
  }

  .agent { position: absolute; left: 30px; top: 118px; }
  .agent__name {
    color: var(--accent);
    font-weight: 700;
    font-size: 19px;
    letter-spacing: 1px;
    text-transform: uppercase;
  }
  .agent__title { color: var(--muted); font-size: 12px; margin-top: 2px; }

  .contact {
    position: absolute;
    left: 30px;
    top: 178px;
    list-style: none;
    color: var(--text);
    font-size: 11.5px;
    line-height: 1.35;
  }
  .contact li { display: flex; gap: 8px; align-items: flex-start; margin-bottom: 3px; }
  .contact svg { width: 12px; height: 12px; fill: var(--accent); flex-shrink: 0; margin-top: 2px; }

  .headshot {
    position: absolute;
    right: 0; top: 22px;
    width: 230px; height: 286px;
    background: radial-gradient(ellipse at 50% 20%, var(--photo-mid) 0%, var(--photo-top) 55%, var(--card) 80%);
  }

  .pattern {
    position: absolute; inset: 0;
    background: linear-gradient(135deg, var(--pattern-a), var(--pattern-b));
  }
  .back-brand {
    position: absolute;
    right: 34px; bottom: 30px;
    display: flex; align-items: center; gap: 10px;
  }
  .back-brand .brand__dot { width: 40px; height: 40px; }
  .back-brand__name {
    color: var(--accent);
    font-weight: 600;
    font-size: 14px;
    letter-spacing: 1.5px;
    text-transform: uppercase;
  }
</style>
</head>
<body>

<section class="card card--front">
  <div class="brand">
    <span class="brand__dot"></span>
    <div class="brand__name">Harborline Realty<br>&amp; Investment Corp.</div>
  </div>

  <div class="agent">
    <div class="agent__name">Miles Tandrow</div>
    <div class="agent__title">Real Estate Agent</div>
  </div>

  <ul class="contact">
    <li>
      <svg viewBox="0 0 24 24"><path d="M12 2a7 7 0 0 0-7 7c0 5 7 13 7 13s7-8 7-13a7 7 0 0 0-7-7zm0 9.5A2.5 2.5 0 1 1 12 6.5a2.5 2.5 0 0 1 0 5z"/></svg>
      <span>5286 N 7200 Suite 208-617<br>Cedar Hollow, UT 84721</span>
    </li>
    <li>
      <svg viewBox="0 0 24 24"><path d="M6.6 10.8a15 15 0 0 0 6.6 6.6l2.2-2.2c.3-.3.7-.4 1-.2 1.1.4 2.3.6 3.6.6.6 0 1 .4 1 1V20c0 .6-.4 1-1 1A17 17 0 0 1 3 4c0-.6.4-1 1-1h3.5c.6 0 1 .4 1 1 0 1.3.2 2.5.6 3.6.1.3 0 .7-.2 1z"/></svg>
      <span>801-555-0162</span>
    </li>
    <li>
      <svg viewBox="0 0 24 24"><path d="M3 5h18v14H3zm2 2v.5l7 4.5 7-4.5V7z"/></svg>
      <span>miles@harborlinehomesite.com</span>
    </li>
    <li>
      <svg viewBox="0 0 24 24"><path d="M12 2a10 10 0 1 0 0 20 10 10 0 0 0 0-20zm6.9 9h-3a15 15 0 0 0-1.4-6 8 8 0 0 1 4.4 6zM12 4c.9 1.3 1.7 3.9 1.9 7h-3.8C10.3 7.9 11.1 5.3 12 4zM9.5 5a15 15 0 0 0-1.4 6h-3a8 8 0 0 1 4.4-6zM5.1 13h3a15 15 0 0 0 1.4 6 8 8 0 0 1-4.4-6zM12 20c-.9-1.3-1.7-3.9-1.900-7h3.8c-.2 3.1-1 5.7-1.9 7zm2.5-1a15 15 0 0 0 1.4-6h3a8 8 0 0 1-4.4 6z"/></svg>
      <span>HarborlineHomesite.com</span>
    </li>
  </ul>

  <div class="headshot" role="img" aria-label="Headshot of Miles Tandrow in a grey plaid suit jacket"></div>
</section>

<section class="card card--back">
  <div class="pattern" role="img" aria-label="Repeating embossed brand pattern in dark gloss and silver foil"></div>
  <div class="back-brand">
    <span class="brand__dot"></span>
    <span class="back-brand__name">Harborline</span>
  </div>
</section>

</body>
</html>
```